Modern design company business card design

We are a design oriented construction firm. The owner is an architect and licensed General Contractor and accomplished furniture designer. We do new home construction and large scale remodeling and office design. We would like a design for our new business cards that is clean and modern, but relatable. We like the bright green color of our logo mixed with different shades of grey. We're also open to reinterpreting the logo.

Target Market(s)

Potential design clients,
Construction clients

Industry/Entity Type

Architecture

Contact Information for Business Card

Tall Maple Design | Build Inc. (optional with logo, Inc. optional)Jeffrey MorganOwner (optional)317.555.0148 cell317.431.8056 officejmorgan@greensquareinc.comwww.greensquareinc.com

Font styles to use
Sans Serif
Other font styles liked:
• Avenir

Requirements
Nice to have
• I like designs that have some continuity between the front and back, i.e. similar layouts or graphic elements that wrap around the card. I tend to prefer horizontal over vertical, but that's not a have to. I also tend to prefer white or recycled paper.

```html
<!DOCTYPE html>
<html lang="en">
<head>
<meta charset="utf-8">
<title>Tall Maple Design | Build — Business Card</title>
<link rel="stylesheet" href="https://fonts.googleapis.com/css2?family=Nunito+Sans:wght@400;700;800&display=swap">
<style>
  :root {
    --backdrop: #e9e8e5;
    --paper: #ffffff;
    --leaf: #3da33f;
    --slate: #5a5c60;
    --slate-dark: #2f3033;
    --ink: #55575b;
    --ink-soft: #7d7f83;
    --rule: #6e7074;
  }
  * { box-sizing: border-box; margin: 0; padding: 0; }
  html, body {
    width: 1200px; height: 913px; overflow: hidden;
    background: var(--backdrop);
    font-family: "Nunito Sans", "Avenir", sans-serif;
  }
  .stage {
    position: relative; width: 1200px; height: 913px;
    display: flex; align-items: center; justify-content: center; gap: 40px;
  }
  .card {
    position: relative; width: 540px; height: 309px; overflow: hidden;
    box-shadow: 0 10px 26px rgba(0,0,0,.18);
  }

  /* Company name */
  .company { position: absolute; display: flex; align-items: center; gap: 12px; }
  .company__dot { width: 12px; height: 12px; border-radius: 50%; background: var(--leaf); flex: none; }
  .company__name { font-weight: 400; font-size: 28px; line-height: 1; letter-spacing: .3px; }

  /* Front */
  .card--front { background: var(--paper); }
  .card--front .company { left: 30px; top: 62px; }
  .card--front .company__name { color: var(--ink-soft); }

  .holder { position: absolute; right: 44px; top: 128px; text-align: right; }
  .holder__name {
    font-weight: 800; font-size: 17px; letter-spacing: .6px; color: var(--ink);
    text-transform: uppercase; line-height: 22px;
  }
  .holder__title {
    font-weight: 400; font-size: 11px; letter-spacing: 1.5px; color: var(--leaf);
    text-transform: uppercase; margin-top: 6px;
  }
  .divider {
    position: absolute; left: 30px; right: 44px; top: 152px;
    height: 1px; background: var(--rule);
  }
  .contacts { position: absolute; left: 30px; top: 172px; list-style: none; }
  .contacts li {
    display: flex; align-items: center; gap: 8px;
    font-size: 13px; line-height: 19px; color: var(--ink); letter-spacing: .2px;
  }
  .contacts svg { width: 11px; height: 11px; fill: var(--leaf); flex: none; }
  .bands { position: absolute; left: 0; bottom: 0; width: 540px; height: 90px; }

  /* Back */
  .card--back { background: linear-gradient(160deg, #77797d 0%, var(--slate) 45%, var(--slate-dark) 100%); }
  .card--back .company { left: 0; right: 0; top: 136px; justify-content: center; }
  .card--back .company__name { color: #ffffff; font-size: 34px; }
</style>
</head>
<body>
<main class="stage">
  <section class="card card--front" aria-label="Card front">
    <div class="company">
      <span class="company__dot"></span>
      <span class="company__name">Tall Maple</span>
    </div>

    <div class="holder">
      <p class="holder__name">Dennis Holloway</p>
      <p class="holder__title">Owner</p>
    </div>
    <div class="divider"></div>

    <ul class="contacts">
      <li><svg viewBox="0 0 12 12"><rect x="3" y="0" width="6" height="12" rx="1"/><rect x="4" y="1.5" width="4" height="7.5" fill="#fff"/></svg>317.555.0172</li>
      <li><svg viewBox="0 0 12 12"><path d="M2.4 0.6 4.6 2.8 3.4 4.6c.8 1.6 2.2 3 3.8 3.8l1.8-1.2 2.2 2.2-1.6 1.8C5 11 1 7 .6 2.2z"/></svg>317.555.0148</li>
      <li><svg viewBox="0 0 12 12"><circle cx="6" cy="6" r="5.5"/><path d="M.5 6h11M6 .5c-3 3-3 8 0 11M6 .5c3 3 3 8 0 11" stroke="#fff" stroke-width=".8" fill="none"/></svg>www.tallmapleinc.example</li>
      <li><svg viewBox="0 0 12 12"><rect x="0" y="2" width="12" height="8"/><path d="M.5 2.5 6 6.5l5.5-4" stroke="#fff" stroke-width=".9" fill="none"/></svg>dholloway@tallmapleinc.example</li>
    </ul>

    <svg class="bands" viewBox="0 0 540 90" preserveAspectRatio="none" aria-hidden="true">
      <rect x="0" y="76" width="540" height="14" fill="var(--leaf)"/>
      <polygon points="318,0 540,0 540,90 342,90 342,24" fill="var(--slate)"/>
    </svg>
  </section>

  <section class="card card--back" aria-label="Card back">
    <div class="company">
      <span class="company__dot"></span>
      <span class="company__name">Tall Maple</span>
    </div>
  </section>
</main>
</body>
</html>
```